I want a website to be designed for our new company, it's an import and export company for variety of things.

please see the attached Logo for our company and the Images for our different sections for our busienss

Target Market(s)

multiple

Coding

Coded - Design and coding required

Number of Pages Required

5+ page

Font styles to use
Sans Serif

Colors

Designer to choose colors to be used in the design.

Requirements
Must have
• KVR GLOBALINKS
• KVR globalinks Trading & Contracting provides various services. The Company offers infrastructure construction, oil, enegy and gas services, agricultural projects, real estate development, travel and tourism, and food processing and trading.
• Civil contracting for infrastructure, residential and heavy projects. Through its main subsidiaries; distribution of general food products, construction chemicals including corrosion inhibitors and electrical machinery; provides catering and travel agency services; ownership and operation of a school; offers human sources services including manpower supply.
• Drilling and Gold Mines Used Machinery, All Kinds of Construction Machinery, Drilling Machines are manufactured and sold.
Nice to have
• good designa and beautiful colours, it has too look professional

```html
<!DOCTYPE html>
<html lang="en">
<head>
<meta charset="utf-8">
<title>KVR Globalinks</title>
<link href="https://fonts.googleapis.com/css2?family=Exo+2:wght@500;600;700&family=Mulish:wght@400;600;700&display=swap" rel="stylesheet">
<style>
:root{
  --ink:#2b2b2b;
  --dark:#1f1f1f;
  --muted:#555;
  --gold:#c9862e;
  --gold-light:#d9a441;
  --rust:#b5621b;
  --grey-bg:#e9e9e9;
  --white:#fff;
  --footer:#1b1b1b;
}
*{margin:0;padding:0;box-sizing:border-box}
html,body{width:1200px;height:3308px;overflow:hidden}
body{position:relative;background:var(--white);font-family:"Mulish",sans-serif;color:var(--ink)}
.abs{position:absolute}
.head{font-family:"Exo 2",sans-serif;font-weight:700;text-transform:uppercase;color:var(--ink)}
.btn{position:absolute;display:flex;align-items:center;justify-content:center;font-family:"Exo 2",sans-serif;font-weight:600;text-transform:uppercase;color:var(--white);border-radius:30px;background:linear-gradient(90deg,var(--gold-light),var(--rust))}

/* hero */
.hero{left:0;top:0;width:1200px;height:612px;background:linear-gradient(180deg,#2a2a2c 0%,#3b3a3a 40%,#4a4037 70%,#1e1d1e 100%)}
.topbar-phone{left:173px;top:26px;display:flex;align-items:center;gap:6px;color:var(--white);font-family:"Exo 2",sans-serif;font-weight:600;font-size:17px}
.phone-dot{width:22px;height:22px;border-radius:50%;background:var(--gold);display:flex;align-items:center;justify-content:center}
.nav a{position:absolute;top:76px;color:var(--white);font-family:"Exo 2",sans-serif;font-weight:500;font-size:15px;text-decoration:none;letter-spacing:.3px}
.nav .active:after{content:"";position:absolute;left:0;top:24px;width:44px;height:3px;background:var(--gold);border-radius:2px}
.brand{left:480px;top:62px;width:220px;text-align:center;font-family:"Exo 2",sans-serif;font-weight:600;font-size:18px;letter-spacing:2px;color:#d8d8d8}
.brand-mark{left:572px;top:24px;width:36px;height:36px;border-radius:50%;border:2px solid #cfcfcf}
.hero-title{left:0;width:1200px;top:292px;text-align:center;font-size:51px;color:var(--white)}
.arrow{top:330px}

/* welcome */
.welcome{left:0;top:603px;width:1200px;height:562px;background:var(--grey-bg)}
.photo-frame{position:absolute;background:var(--white);padding:9px;box-shadow:0 2px 8px rgba(0,0,0,.18)}
.photo{width:100%;height:100%}
.welcome-title{left:629px;top:684px;font-size:37px;line-height:40px}
.welcome-text{left:629px;top:786px;width:400px;font-size:13.3px;line-height:24px;text-align:justify;color:var(--muted)}

/* services */
.section-title{left:0;width:1200px;text-align:center;font-size:36px}
.services-lead{left:0;width:1200px;top:1302px;text-align:center;font-size:13.3px;line-height:24px;color:var(--muted)}
.card{position:absolute;width:203px;height:224px;background:var(--white);border:1px solid #e3e3e3;box-shadow:0 1px 4px rgba(0,0,0,.08)}
.card .photo{height:157px}
.card p{height:66px;display:flex;align-items:center;justify-content:center;text-align:center;font-family:"Exo 2",sans-serif;font-size:14px;line-height:19px;color:var(--ink)}

/* banner */
.banner{left:0;top:1944px;width:1200px;height:406px;background:linear-gradient(90deg,#2b2624 0%,#4a3426 45%,#6a3a22 70%,#3c2720 100%)}
.banner-title{left:0;width:1200px;top:2073px;text-align:center;font-size:31px;line-height:36px;color:var(--white)}
.btn-outline{background:none;border:2px solid var(--white)}

/* blog */
.post-title{font-family:"Exo 2",sans-serif;font-weight:700;font-size:19px;line-height:24px;text-transform:uppercase;color:#3a3a3a}
.post-text{font-size:11px;line-height:19px;color:var(--muted)}
.post-date{display:flex;align-items:center;gap:5px;font-family:"Exo 2",sans-serif;font-weight:600;font-size:13px;color:var(--gold)}

/* footer */
.footer{left:0;top:2990px;width:1200px;height:318px;background:var(--footer)}
.footer-brand{left:172px;top:3082px;display:flex;align-items:center;gap:10px;font-family:"Exo 2",sans-serif;font-weight:600;font-size:22px;letter-spacing:2px;color:#e2e2e2}
.footer-brand span.dot{width:30px;height:30px;border-radius:50%;border:2px solid #e2e2e2}
.foot-h{font-family:"Exo 2",sans-serif;font-weight:600;font-size:16px;color:var(--white)}
.foot-line{display:flex;gap:16px;align-items:flex-start;font-size:11px;line-height:19px;color:#cfcfcf}
.news{left:738px;top:3071px;width:290px;height:38px;display:flex;border:1px solid #cfcfcf;border-radius:3px;overflow:hidden}
.news span{flex:1;background:var(--footer);color:var(--white);font-size:11px;padding:12px 10px}
.news b{width:82px;background:linear-gradient(90deg,var(--gold-light),var(--rust));color:var(--white);font-family:"Exo 2",sans-serif;font-weight:600;font-size:12px;display:flex;align-items:center;justify-content:center}
.social{left:738px;top:3172px;display:flex;gap:18px}
.social i{display:block;width:15px;height:15px;border-radius:50%;background:#e6e6e6}
.copy{left:0;width:1200px;top:3262px;text-align:center;font-size:12.5px;color:#d8d8d8}
</style>
</head>
<body>

<!-- hero -->
<div class="abs hero" role="img" aria-label="Offshore supply vessel beside an oil drilling platform at dusk"></div>
<div class="abs topbar-phone"><span class="phone-dot"><svg width="11" height="11" viewBox="0 0 24 24"><path fill="#fff" d="M6.6 10.8a15 15 0 0 0 6.6 6.6l2.2-2.2c.3-.3.7-.4 1-.2 1.1.4 2.3.6 3.6.6.6 0 1 .4 1 1V20c0 .6-.4 1-1 1A17 17 0 0 1 3 4c0-.6.4-1 1-1h3.5c.6 0 1 .4 1 1 0 1.3.2 2.5.6 3.6.1.3 0 .7-.2 1z"/></svg></span>PH: 020 555 0148</div>
<nav class="nav">
  <a class="active" style="left:175px">HOME</a>
  <a style="left:250px">SERVICES</a>
  <a style="left:342px">OUR WORKS</a>
  <a style="left:735px">MANUFACTURE</a>
  <a style="left:879px">ABOUT</a>
  <a style="left:959px">CONTACT</a>
</nav>
<span class="abs brand-mark"></span>
<div class="abs brand">KVR GLOBALINKS</div>
<svg class="abs" style="left:970px;top:28px" width="18" height="18" viewBox="0 0 24 24" fill="none" stroke="#fff" stroke-width="2"><circle cx="10" cy="10" r="7"/><path d="M15 15l6 6"/></svg>
<svg class="abs" style="left:1007px;top:26px" width="20" height="20" viewBox="0 0 24 24" fill="none" stroke="#fff" stroke-width="2"><circle cx="12" cy="8" r="5"/><path d="M3 22c1-5 5-8 9-8s8 3 9 8"/></svg>
<h1 class="abs head hero-title">KVR GLOBALINKS</h1>
<div class="btn" style="left:518px;top:373px;width:164px;height:44px;font-size:18px">Get Started</div>
<svg class="abs arrow" style="left:42px" width="20" height="38" viewBox="0 0 20 38" fill="none" stroke="#fff" stroke-width="2"><path d="M18 2L2 19l16 17"/></svg>
<svg class="abs arrow" style="left:1140px" width="20" height="38" viewBox="0 0 20 38" fill="none" stroke="#fff" stroke-width="2"><path d="M2 2l16 17L2 36"/></svg>

<!-- welcome -->
<div class="abs welcome"></div>
<svg class="abs" style="left:0;top:566px" width="1200" height="46" viewBox="0 0 1200 46"><defs><linearGradient id="g1" x1="0" x2="1"><stop offset="0" stop-color="#d9a441"/><stop offset="1" stop-color="#b5621b"/></linearGradient></defs><polygon points="0,44 1200,6 1200,37 0,46" fill="url(#g1)"/><polygon points="0,46 1200,37 1200,46" fill="#e9e9e9"/></svg>
<div class="photo-frame" style="left:255px;top:821px;width:344px;height:240px"><div class="photo" role="img" aria-label="Aerial view of a large modern building complex" style="background:linear-gradient(135deg,#8a8f88,#c9cbc4 50%,#6f7a6a)"></div></div>
<div class="photo-frame" style="left:163px;top:678px;width:357px;height:264px"><div class="photo" role="img" aria-label="Yellow drilling rig working in a snowy pine forest" style="background:linear-gradient(135deg,#1f3550,#5a7aa0 40%,#c9a72a 65%,#2a2c2e)"></div></div>
<h2 class="abs head welcome-title">Welcome to<br>KVR Globalinks</h2>
<p class="abs welcome-text">Sed ut perspiciatis unde omnis iste natus error sit voluptatem accusantium doloremque laudantium, totam rem aperiam, eaque ipsa quae ab illo inventore veritatis et quasi architecto beatae vitae dicta sunt explicabo. Nemo enim ipsam voluptatem quia voluptas sit aspernatur aut odit aut fugit, sed quia consequuntur magni dolores eos qui ratione voluptatem sequi nesciunt. Neque porro quisquam est, qui dolorem ipsum quia dolor sit amet, consectetur, adipisci velit, sed quia.</p>
<div class="btn" style="left:629px;top:997px;width:114px;height:36px;font-size:13px;text-transform:uppercase">Read More</div>

<!-- services -->
<h2 class="abs head section-title" style="top:1240px">Our Services</h2>
<p class="abs services-lead">Sed ut perspiciatis unde omnis iste natus error sit voluptatem accusantium<br>doloremque laudantium, totam rem aperiam, eaque ipsa quae.</p>

<div class="card" style="left:172px;top:1386px"><div class="photo" role="img" aria-label="Drilling rig in a forest" style="background:linear-gradient(135deg,#26405e,#6f8fb0 45%,#caa62c 70%,#3a3a34)"></div><p>Infrastructure<br>Construction</p></div>
<div class="card" style="left:389px;top:1386px"><div class="photo" role="img" aria-label="Offshore oil platform at sea" style="background:linear-gradient(180deg,#4a6a70,#2c4a50 60%,#1f3a3f)"></div><p>Oil</p></div>
<div class="card" style="left:606px;top:1386px"><div class="photo" role="img" aria-label="Wind turbines at sunset" style="background:linear-gradient(180deg,#5fa3b0,#c9c98a 55%,#e8b040 70%,#7a5a2a)"></div><p>Energy and<br>Gas Services</p></div>
<div class="card" style="left:823px;top:1386px"><div class="photo" role="img" aria-label="Tractor spraying a green field" style="background:linear-gradient(160deg,#2f4a24,#4f8a2e 50%,#2a4a1e)"></div><p>Agricultural Projects</p></div>

<div class="card" style="left:172px;top:1630px"><div class="photo" role="img" aria-label="Aerial view of a real estate development" style="background:linear-gradient(135deg,#6f7a66,#c7c9c1 50%,#5c6a52)"></div><p>Real Estate<br>Development</p></div>
<div class="card" style="left:389px;top:1630px"><div class="photo" role="img" aria-label="Beach chairs under an umbrella at sunset" style="background:linear-gradient(180deg,#e9b58a,#f2c89a 45%,#c4622a 75%,#8a4020)"></div><p>Travel and Tourism</p></div>
<div class="card" style="left:606px;top:1630px"><div class="photo" role="img" aria-label="Assortment of fresh and packaged foods" style="background:linear-gradient(135deg,#e8e0d0,#c9402a 35%,#4a8a2e 60%,#e0c050)"></div><p>Food Processing</p></div>
<div class="card" style="left:823px;top:1630px"><div class="photo" role="img" aria-label="Container ship at sea seen from above" style="background:linear-gradient(135deg,#1f4a4c,#2a6a6a 50%,#c9502a 70%,#1f4a4c)"></div><p>Trading</p></div>

<!-- banner -->
<div class="abs banner" role="img" aria-label="Oil pump jacks silhouetted over hills at dusk"></div>
<svg class="abs" style="left:0;top:1944px" width="1200" height="30" viewBox="0 0 1200 30"><polygon points="0,0 1200,0 0,8" fill="#fff"/><polygon points="0,8 1200,0 1200,8 0,28" fill="#b5621b"/></svg>
<svg class="abs" style="left:0;top:2300px" width="1200" height="50" viewBox="0 0 1200 50"><defs><linearGradient id="g2" x1="0" x2="1"><stop offset="0" stop-color="#b5621b"/><stop offset="1" stop-color="#d9a441"/></linearGradient></defs><polygon points="0,48 1200,10 1200,38" fill="url(#g2)"/><polygon points="0,48 1200,38 1200,50 0,50" fill="#fff"/></svg>
<h2 class="abs head banner-title">Drilling Machines are<br>Manufactured</h2>
<div class="btn btn-outline" style="left:513px;top:2169px;width:174px;height:44px;font-size:18px">Get Started</div>

<!-- blog -->
<h2 class="abs head section-title" style="top:2406px">Latest Blog</h2>
<div class="abs" role="img" aria-label="Offshore oil rig lit up at twilight" style="left:172px;top:2494px;width:415px;height:276px;background:linear-gradient(180deg,#2a4a7a,#5a7ab0 40%,#1f3a6a 70%,#c99a40 85%,#1a2a4a)"></div>
<div class="abs" style="left:172px;top:2788px;width:415px">
  <h3 class="post-title">Finibus Bonorum et Malorum</h3>
  <p class="post-text" style="margin-top:6px">Sed ut perspiciatis undloree omnis iste natus error sit voluptatem accusaloren tium doloremque laudantium, totloram rem aperiam, eaque ipsa.</p>
  <div class="post-date" style="margin-top:10px"><svg width="16" height="15" viewBox="0 0 16 15" fill="none" stroke="#c9862e" stroke-width="1.3"><rect x="1" y="2" width="14" height="12"/><path d="M1 6h14M5 0v4M11 0v4"/></svg>JAN 18 2020</div>
</div>

<div class="abs" role="img" aria-label="Excavator breaking rock at a site" style="left:607px;top:2494px;width:206px;height:187px;background:linear-gradient(160deg,#7a8aa8,#3a4a6a 50%,#2a2a30)"></div>
<div class="abs" style="left:830px;top:2512px;width:200px">
  <h3 class="post-title">Finibus Bonorum et Malorum</h3>
  <p class="post-text" style="margin-top:6px">Sed ut perspiciatis undloree omnis iste natus error sit voluptatem accusaloren tium doloremque laudantium, totloram rem aperiam, eaque ipsa.</p>
  <div class="post-date" style="margin-top:10px"><svg width="16" height="15" viewBox="0 0 16 15" fill="none" stroke="#c9862e" stroke-width="1.3"><rect x="1" y="2" width="14" height="12"/><path d="M1 6h14M5 0v4M11 0v4"/></svg>JAN 18 2020</div>
</div>

<div class="abs" role="img" aria-label="Two engineers in safety gear reviewing a refinery" style="left:607px;top:2699px;width:206px;height:187px;background:linear-gradient(160deg,#c9c3b0,#8a8a7a 50%,#b8c030 80%,#4a4a40)"></div>
<div class="abs" style="left:830px;top:2716px;width:200px">
  <h3 class="post-title">Finibus Bonorum et Malorum</h3>
  <p class="post-text" style="margin-top:6px">Sed ut perspiciatis undloree omnis iste natus error sit voluptatem accusaloren tium doloremque laudantium, totloram rem aperiam, eaque ipsa.</p>
  <div class="post-date" style="margin-top:10px"><svg width="16" height="15" viewBox="0 0 16 15" fill="none" stroke="#c9862e" stroke-width="1.3"><rect x="1" y="2" width="14" height="12"/><path d="M1 6h14M5 0v4M11 0v4"/></svg>JAN 18 2020</div>
</div>

<!-- footer -->
<div class="abs footer"></div>
<div class="abs footer-brand"><span class="dot"></span>KVR GLOBALINKS</div>

<div class="abs foot-h" style="left:493px;top:3032px">Contact</div>
<div class="abs foot-line" style="left:493px;top:3064px"><svg width="16" height="20" viewBox="0 0 16 20" fill="none" stroke="#cfcfcf" stroke-width="1.3"><path d="M8 19s7-7 7-11A7 7 0 0 0 1 8c0 4 7 11 7 11z"/><circle cx="8" cy="8" r="2.5"/></svg><span>214 Harbour View Road,<br>Eastgate, Marlow</span></div>
<div class="abs foot-line" style="left:493px;top:3117px"><svg width="20" height="20" viewBox="0 0 24 24" fill="none" stroke="#cfcfcf" stroke-width="1.3"><path d="M6.6 10.8a15 15 0 0 0 6.6 6.6l2.2-2.2c.3-.3.7-.4 1-.2 1.1.4 2.3.6 3.6.6.6 0 1 .4 1 1V20c0 .6-.4 1-1 1A17 17 0 0 1 3 4c0-.6.4-1 1-1h3.5c.6 0 1 .4 1 1 0 1.3.2 2.5.6 3.6.1.3 0 .7-.2 1z"/></svg><span>8 800 555 010 11<br>8 800 555 024 88</span></div>
<div class="abs foot-line" style="left:493px;top:3170px"><svg width="22" height="16" viewBox="0 0 22 16" fill="none" stroke="#cfcfcf" stroke-width="1.3"><rect x="1" y="1" width="20" height="14"/><path d="M1 1l10 8 10-8"/></svg><span>info@kvrglobalinks.example<br>founder@kvrglobalinks.example</span></div>

<div class="abs foot-h" style="left:740px;top:3032px">Newsletter</div>
<div class="abs news"><span>Email:</span><b>SIGN UP</b></div>
<div class="abs foot-h" style="left:740px;top:3137px">Follow Us</div>
<div class="abs social" aria-label="Social links"><i></i><i></i><i></i><i></i><i></i></div>

<div class="abs" style="left:172px;top:3240px;width:856px;height:1px;background:#3a3a3a"></div>
<div class="abs copy">© 2020 KVR Globalinks. All rights reserved.</div>

</body>
</html>
```